Golden Coat All-Purpose Breading Bag Design

Our client, Halvern Food Products, is looking to re-design the packaging for their product, Pellham's Golden Coat. Goldn Coat is an all-purpose food breading mix.

Halvern Foods has a registered trademark for this product, but they have not been using it for this particular 10 pound bag. They want to get the trademark onto the bag and also give the bag an updated look. They would like to continue to use the same red and blue colors. This 10 pound bag is not available on store shelves; it is sold to food service distributors who sell to restaurants.

All of the copy on the existing bag is still relevant, so we will want to incoprporate it into the bag design. Once these bags are filled with product, the tops get folded over about 1 inch and then sewn shut with thread.

Eventually, we will need the design applied to the Bag Template file attached, but that isn't important until a design is selected.

Target Market(s)

Restaurants

Industry/Entity Type

Food Manufacturing

Colors
0054AA
0677BA
7BADD7
CADEEF
E8F1F8
EB3D1F
EC4F4E
F09395
F8D3D4
FCEDEE

Requirements
Must have
• Trademark introduced to the design

```html
<!DOCTYPE html>
<html lang="en">
<head>
<meta charset="utf-8">
<title>Golden Coat All-Purpose Breading – Bag Layout</title>
<link href="https://fonts.googleapis.com/css2?family=Montserrat:wght@400;500;600;700;800&display=swap" rel="stylesheet">
<style>
  :root {
    --red: #EB3D1F;
    --blue: #0054AA;
    --pink: #F8D3D4;
    --sky: #CADEEF;
    --cream: #FCEDEE;
    --edge: #E8338A;
    --ground: #7a7a7a;
    --navy: #1d2f4d;
  }
  * { box-sizing: border-box; margin: 0; padding: 0; }
  html, body { width: 1200px; height: 900px; overflow: hidden; }
  body {
    background: var(--ground);
    font-family: "Montserrat", sans-serif;
    position: relative;
  }
  .panel { position: absolute; top: 73px; height: 599px; }
  .panel--pink { background: var(--pink); }
  .panel--sky { background: var(--sky); }
  .panel--side-a { left: 75px; width: 205px; border-left: 2px solid var(--edge); }
  .panel--front { left: 280px; width: 342px; }
  .panel--side-b { left: 622px; width: 186px; }
  .panel--back { left: 808px; width: 340px; }

  .seal {
    position: absolute; border-radius: 50%;
    display: flex; flex-direction: column; align-items: center; justify-content: center;
    color: var(--cream); text-align: center; font-weight: 700; line-height: 1.05;
  }
  .seal--small { width: 156px; height: 156px; background: var(--blue); font-size: 20px; }
  .seal--large { width: 282px; height: 282px; background: var(--red); font-size: 40px; }
  .seal__tag { font-size: .32em; letter-spacing: .12em; margin-top: .9em; }

  .box { position: absolute; border: 2px solid; }
  .box--red { border-color: var(--red); color: var(--red); }
  .box--blue { border-color: var(--blue); color: var(--blue); }

  .about {
    left: 33px; top: 322px; width: 157px; height: 247px; overflow: hidden;
    font-size: 10.2px; line-height: 12.4px; text-align: center; padding: 10px 5px;
  }
  .about p + p { margin-top: 12px; }

  .facts { left: 18px; top: 354px; width: 304px; height: 200px; display: flex; flex-direction: column; }
  .facts__row { border-bottom: 2px solid var(--blue); text-align: center; }
  .facts__slogan { height: 53px; padding-top: 9px; font-size: 13.5px; font-weight: 500; color: #3b4756; line-height: 18px; }
  .facts__slogan .hi-red { color: var(--red); font-weight: 700; }
  .facts__slogan .hi-blue { color: var(--blue); font-weight: 700; }
  .facts__claim { height: 27px; line-height: 25px; font-size: 9.5px; letter-spacing: .18em; font-weight: 600; color: #3b4756; }
  .facts__ingredients { height: 68px; padding-top: 7px; }
  .heading {
    display: block; margin: 0 auto; font-weight: 600; letter-spacing: .12em;
    font-size: 12.5px; color: var(--blue); border-bottom: 2px solid var(--blue);
    padding-bottom: 3px;
  }
  .facts__ingredients .heading { width: 272px; }
  .facts__ingredients p { font-size: 10.3px; color: #3b4756; margin-top: 7px; line-height: 15px; }
  .facts__foot { flex: 1; display: flex; }
  .facts__foot > div { display: flex; flex-direction: column; justify-content: center; align-items: center; text-align: center; }
  .foot__yield { width: 110px; font-size: 7.5px; color: #3b4756; line-height: 10px; }
  .foot__weight { width: 72px; background: var(--blue); color: #fff; font-size: 8px; }
  .foot__weight strong { font-size: 12px; font-weight: 700; margin-top: 2px; }
  .foot__maker { flex: 1; font-size: 6.5px; color: #3b4756; line-height: 9px; }
  .foot__maker strong { font-size: 7.5px; color: #3b4756; }

  .directions { left: 15px; top: 346px; width: 156px; height: 208px; display: flex; flex-direction: column; }
  .directions__main { height: 159px; border-bottom: 2px solid var(--red); padding: 12px 10px 0; }
  .directions__kicker { text-align: center; font-size: 9px; letter-spacing: .14em; font-weight: 600; color: #222; }
  .directions__title { text-align: center; font-size: 16px; letter-spacing: .16em; font-weight: 600; margin-top: 3px; padding-bottom: 6px; border-bottom: 2px solid var(--red); }
  .directions ul { list-style: none; margin-top: 8px; }
  .directions li { font-size: 9.5px; color: #333; line-height: 12px; padding-left: 14px; position: relative; margin-bottom: 6px; }
  .directions li::before { content: ""; position: absolute; left: 2px; top: 4px; width: 5px; height: 5px; border-radius: 50%; background: var(--red); }
  .directions__tip { flex: 1; display: flex; align-items: center; justify-content: center; text-align: center; font-size: 9.5px; color: #333; line-height: 12px; padding: 0 8px; }

  .usage { left: 17px; top: 353px; width: 305px; height: 201px; display: flex; flex-direction: column; }
  .usage__method { height: 121px; border-bottom: 2px solid var(--blue); text-align: center; padding-top: 9px; }
  .usage__method > span { display: block; line-height: 1; }
  .usage__for, .usage__and { font-size: 16px; font-weight: 600; color: #2a2f38; letter-spacing: .04em; }
  .usage__big { font-size: 26px; font-weight: 800; margin: 2px 0; }
  .usage__big--red { color: var(--red); }
  .usage__big--blue { color: var(--blue); }
  .usage__note { font-size: 8px; color: #2a2f38; letter-spacing: .08em; margin-top: 1px; }
  .usage__list { flex: 1; padding-top: 10px; text-align: center; }
  .usage__list .heading { width: 270px; }
  .usage__list p { font-size: 10.3px; color: #333; line-height: 15px; margin-top: 9px; }

  .tab { position: absolute; left: 310px; top: 672px; width: 285px; height: 168px; background: var(--sky); }
  .tab__slogan {
    position: absolute; left: 15px; top: 20px; width: 253px; height: 125px;
    background: var(--blue); border: 2px solid var(--navy);
    display: flex; flex-direction: column; align-items: center; justify-content: center;
    color: #fff; font-size: 12.5px; line-height: 17px; text-align: center; font-weight: 500;
  }
  .tab__slogan strong { font-weight: 700; }
</style>
</head>
<body>
  <section class="panel panel--pink panel--side-a">
    <div class="seal seal--small" style="left:35px;top:109px;">Pellham's<br>Golden Coat<span class="seal__tag">ALL PURPOSE BREADING</span></div>
    <div class="box box--red about">
      <p>Pellham's Golden Coat is a prepared formula of pure foods that enables you to fry chicken from the raw to the well done in ten minutes. It seals in all the natural juice and creates a very thin crunchy coating which the fat does not penetrate- thereby using much less fat than ordinary frying methods.</p>
      <p>This formula is an all-dry mix to be used on anything breaded- fish, oysters, shrimp, veal and chicken fried steak.</p>
    </div>
  </section>

  <section class="panel panel--sky panel--front">
    <div class="seal seal--large" style="left:30px;top:54px;">Pellham's<br>Golden Coat<span class="seal__tag">ALL PURPOSE BREADING</span></div>
    <div class="box box--blue facts">
      <div class="facts__row facts__slogan">CHICKEN FRIED <span class="hi-red">THE GOLDEN COAT WAY</span><br>IS THE FRIED CHICKEN <span class="hi-blue">THE RIGHT WAY</span></div>
      <div class="facts__row facts__claim">SEALS JUICE IN- GREASE OUT</div>
      <div class="facts__row facts__ingredients">
        <span class="heading">INGREDIENTS</span>
        <p>flour, salt, non-fat milk solids, egg yolk, baking powder,<br>corn starch, sugar and pepper</p>
      </div>
      <div class="facts__foot">
        <div class="foot__yield">Cooks two-pound<br>chicken well done<br>in 10 minutes (deep fat)</div>
        <div class="foot__weight">Net Wt.<strong>10 Lbs</strong></div>
        <div class="foot__maker"><span>by <strong>Halvern Food Products</strong></span>4870 Orchard Lane<br>Millbrook, Ohio 45102</div>
      </div>
    </div>
  </section>

  <section class="panel panel--pink panel--side-b">
    <div class="seal seal--small" style="left:15px;top:109px;">Pellham's<br>Golden Coat<span class="seal__tag">ALL PURPOSE BREADING</span></div>
    <div class="box box--red directions">
      <div class="directions__main">
        <div class="directions__kicker">NOTHING TO ADD</div>
        <div class="directions__title">DIRECTIONS</div>
        <ul>
          <li>Wet all foods in water</li>
          <li>Place in dry dip, coating thoroughly</li>
          <li>Deep fry at 350°F for 10 minutes</li>
        </ul>
      </div>
      <div class="directions__tip">For best results double dip onion rings and oysters</div>
    </div>
  </section>

  <section class="panel panel--sky panel--back">
    <div class="seal seal--large" style="left:40px;top:54px;">Pellham's<br>Golden Coat<span class="seal__tag">ALL PURPOSE BREADING</span></div>
    <div class="box box--blue usage">
      <div class="usage__method">
        <span class="usage__for">FOR</span>
        <span class="usage__big usage__big--red">DEEP FAT</span>
        <span class="usage__and">AND</span>
        <span class="usage__big usage__big--blue">PAN FRYING</span>
        <span class="usage__note">(slightly longer on pan frying)</span>
      </div>
      <div class="usage__list">
        <span class="heading">CAN BE USED FOR</span>
        <p>chicken, steaks, chops, tenderloin. fish, shrimp,<br>oyster and other sea foods, onion rings and vegetables</p>
      </div>
    </div>
  </section>

  <section class="tab">
    <div class="tab__slogan">
      <span>CHICKEN FRIED</span>
      <strong>THE GOLDEN COAT WAY</strong>
      <span>IS THE FRIED CHICKEN</span>
      <strong>THE RIGHT WAY</strong>
    </div>
  </section>
</body>
</html>
```